Website Design - TallyPorchHelpers.net

PLEASE CHECK WORD DOCUMENT ATTACHED FOR WEBSITE FLOW.

Target Market(s)

REAL ESTATE AGENTS ARE THE TARGET MARKET

Industry/Entity Type

Real Estate

Coding

Coded - Design and coding required

Number of Pages Required

4 page

Colors

Designer to choose colors to be used in the design.

Requirements
Must have
• WE LIKE RED LOGO ATTACHED
Nice to have
• PLEASE CHECK WORD DOCUMENT ATTACHED FOR WEBSITE FLOW.
Should not have

```html
<!DOCTYPE html>
<html lang="en">
<head>
<meta charset="utf-8">
<title>TallyPorchHelpers.net</title>
<link rel="stylesheet" href="https://fonts.googleapis.com/css2?family=Poppins:wght@500;600;700&family=Roboto:wght@400;500&display=swap">
<style>
:root{
  --red:#e8242a;
  --ink:#1c1c1c;
  --dark:#1b1b1b;
  --muted:#5a5a5a;
  --soft:#efefef;
  --white:#ffffff;
  --foot-text:#a8a8a8;
}
*{box-sizing:border-box;margin:0;padding:0}
html,body{width:951px;height:1200px;overflow:hidden;background:var(--white);font-family:"Roboto",sans-serif;color:var(--ink)}
.page{position:relative;width:951px;height:1200px}

.site-header{position:absolute;top:0;left:0;width:951px;height:64px;background:var(--white)}
.brand{position:absolute;left:186px;top:20px;display:flex;align-items:center;gap:6px}
.brand-mark{width:22px;height:22px;background:var(--red)}
.brand-name{font-family:"Poppins",sans-serif;font-weight:700;font-size:12px;color:var(--red);line-height:1.05;width:60px}
.main-nav{position:absolute;left:313px;top:26px;display:flex;gap:24px;font-size:8.5px;letter-spacing:.3px;color:#2a2a2a;font-weight:500}
.call-box{position:absolute;left:653px;top:0;width:298px;height:64px;background:var(--red);color:var(--white);display:flex;align-items:center;padding-left:16px;gap:8px}
.call-box small{display:block;font-size:8px}
.call-box strong{display:block;font-size:11.5px;font-weight:500;letter-spacing:.2px}

.hero{position:absolute;top:64px;left:0;width:951px;height:411px;background:linear-gradient(100deg,#d9a270 0%,#8c5a3e 30%,#7a4e3a 55%,#5b4a3e 78%,#2f2a28 100%)}
.hero-copy{position:absolute;top:170px;left:0;width:951px;text-align:center;color:var(--white)}
.hero-copy h1{font-family:"Poppins",sans-serif;font-weight:700;font-size:25px;margin-bottom:7px}
.hero-copy p{font-size:14.5px;line-height:18px;font-weight:500}

.audience{position:absolute;top:475px;left:0;width:951px;height:170px}
.section-title{font-family:"Poppins",sans-serif;font-weight:600;font-size:16px;text-align:center;color:var(--ink)}
.audience .section-title{margin-top:36px}
.audience-options{position:absolute;top:81px;left:186px;display:flex;gap:15px}
.option{width:183px;height:49px;border-radius:3px;background:var(--dark);color:var(--white);font-size:11.5px;display:flex;align-items:center;justify-content:center}
.option.is-active{background:var(--red)}

.packages{position:absolute;top:645px;left:0;width:951px;height:418px;background:var(--soft)}
.packages .section-title{margin-top:35px}
.package-list{position:absolute;top:81px;left:186px;display:flex;gap:7.5px}
.package{width:110px;height:297px;background:var(--white);border-radius:3px;position:relative;overflow:hidden}
.package.is-featured{box-shadow:0 2px 8px rgba(0,0,0,.18)}
.package-head{height:54px;position:relative}
.package-head svg{position:absolute;top:0;left:0}
.package-head h3{position:relative;font-family:"Poppins",sans-serif;font-weight:600;font-size:11.5px;color:var(--white);text-align:center;padding-top:11px}
.features{list-style:none;padding:10px 8px 0 10px}
.features li{display:flex;gap:3px;font-size:8.3px;line-height:12px;color:#444;margin-bottom:12px}
.features svg{flex:none;margin-top:2px}
.signup{display:block;margin:0 auto;width:89px;height:26px;background:var(--dark);color:var(--white);font-size:8.5px;font-weight:500;text-align:center;line-height:26px;border-radius:2px}
.is-featured .signup{background:var(--red)}
.package-note{font-size:6.6px;color:#777;text-align:center;line-height:9.6px;margin-top:9px;padding:0 10px}

.site-footer{position:absolute;top:1063px;left:0;width:951px;height:137px;background:var(--dark);color:var(--foot-text)}
.contact-row{position:absolute;top:28px;left:186px;display:flex;font-size:8.3px;line-height:12.5px}
.contact{display:flex;gap:8px;align-items:flex-start}
.contact.address{width:149px}
.contact.phone{width:150px}
.social{position:absolute;left:671px;top:32px;display:flex;gap:5px}
.social span{width:20px;height:20px;border:1.3px solid var(--foot-text);border-radius:50%}
.footer-rule{position:absolute;top:94px;left:0;width:951px;height:1px;background:#2c2c2c}
.footer-brand{position:absolute;top:87px;left:445px;width:60px;height:16px;background:var(--dark);display:flex;align-items:center;justify-content:center;gap:3px}
.footer-brand i{width:7px;height:7px;background:var(--red)}
.footer-brand b{font-family:"Poppins",sans-serif;font-weight:700;font-size:6px;color:var(--red)}
.legal{position:absolute;top:112px;left:186px;width:579px;display:flex;justify-content:space-between;font-size:8.3px}
</style>
</head>
<body>
<div class="page">

<header class="site-header">
  <div class="brand"><span class="brand-mark"></span><span class="brand-name">Tally Porch Helpers</span></div>
  <nav class="main-nav"><span>HOW IT WORKS</span><span>SERVICE AREA</span><span>PRICING</span><span>ABOUT US</span><span>FAQ</span></nav>
  <div class="call-box">
    <svg width="20" height="20" viewBox="0 0 24 24" fill="none" stroke="#fff" stroke-width="1.4"><path d="M5 3h4l2 5-2.5 1.5a11 11 0 0 0 6 6L16 13l5 2v4a2 2 0 0 1-2 2A17 17 0 0 1 3 5a2 2 0 0 1 2-2z"/></svg>
    <div><small>Call Us Today</small><strong>1800 555 0142</strong></div>
  </div>
</header>

<section class="hero" role="img" aria-label="Photo of a couple shaking hands with a real estate agent outside a house, with an open house sign on the lawn">
  <div class="hero-copy">
    <h1>Helping agents save time and money.</h1>
    <p>We place signs and boost foot traffic to your open houses<br>using proven marketing techniques.</p>
  </div>
</section>

<section class="audience">
  <h2 class="section-title">Choose The Option Below That Best Describes You</h2>
  <div class="audience-options">
    <div class="option">I’m a Full On Brokerage</div>
    <div class="option is-active">I’m &nbsp;an Ind. Broker With A Team</div>
    <div class="option">I Need Sign Placement Asap</div>
  </div>
</section>

<section class="packages">
  <h2 class="section-title">Choose Your Package</h2>
  <div class="package-list">
    <article class="package">
      <div class="package-head"><svg width="110" height="54" viewBox="0 0 110 54"><path d="M0 0H110V50Q85 36 55 48T0 50Z" fill="#e8242a"/></svg><h3>5 SIGNS</h3></div>
      <ul class="features">
        <li><svg width="8" height="8" viewBox="0 0 8 8"><rect x=".5" y=".5" width="7" height="7" fill="none" stroke="#bbb"/><path d="M1.5 4l2 2 4-5" fill="none" stroke="#e8242a" stroke-width="1.3"/></svg>Place signs strategically in best areas according to where the open house is located</li>
        <li><svg width="8" height="8" viewBox="0 0 8 8"><rect x=".5" y=".5" width="7" height="7" fill="none" stroke="#bbb"/><path d="M1.5 4l2 2 4-5" fill="none" stroke="#e8242a" stroke-width="1.3"/></svg>Pick Up the signs after the open house</li>
        <li><svg width="8" height="8" viewBox="0 0 8 8"><rect x=".5" y=".5" width="7" height="7" fill="none" stroke="#bbb"/><path d="M1.5 4l2 2 4-5" fill="none" stroke="#e8242a" stroke-width="1.3"/></svg>Store custom signs for you if needed</li>
      </ul>
      <span class="signup">SIGN UP</span>
      <p class="package-note">Sign Up For A Subscription And Get These Marketing Services For Free</p>
    </article>
    <article class="package">
      <div class="package-head"><svg width="110" height="54" viewBox="0 0 110 54"><path d="M0 0H110V50Q85 36 55 48T0 50Z" fill="#e8242a"/></svg><h3>10 SIGNS</h3></div>
      <ul class="features">
        <li><svg width="8" height="8" viewBox="0 0 8 8"><rect x=".5" y=".5" width="7" height="7" fill="none" stroke="#bbb"/><path d="M1.5 4l2 2 4-5" fill="none" stroke="#e8242a" stroke-width="1.3"/></svg>Place signs strategically in best areas according to where the open house is located</li>
        <li><svg width="8" height="8" viewBox="0 0 8 8"><rect x=".5" y=".5" width="7" height="7" fill="none" stroke="#bbb"/><path d="M1.5 4l2 2 4-5" fill="none" stroke="#e8242a" stroke-width="1.3"/></svg>Pick Up the signs after the open house</li>
        <li><svg width="8" height="8" viewBox="0 0 8 8"><rect x=".5" y=".5" width="7" height="7" fill="none" stroke="#bbb"/><path d="M1.5 4l2 2 4-5" fill="none" stroke="#e8242a" stroke-width="1.3"/></svg>Store custom signs for you if needed</li>
      </ul>
      <span class="signup">SIGN UP</span>
      <p class="package-note">Sign Up For A Subscription And Get These Marketing Services For Free</p>
    </article>
    <article class="package is-featured">
      <div class="package-head"><svg width="110" height="54" viewBox="0 0 110 54"><path d="M0 0H110V50Q85 36 55 48T0 50Z" fill="#e8242a"/></svg><h3>15 SIGNS</h3></div>
      <ul class="features">
        <li><svg width="8" height="8" viewBox="0 0 8 8"><rect x=".5" y=".5" width="7" height="7" fill="none" stroke="#bbb"/><path d="M1.5 4l2 2 4-5" fill="none" stroke="#e8242a" stroke-width="1.3"/></svg>Place signs strategically in best areas according to where the open house is located</li>
        <li><svg width="8" height="8" viewBox="0 0 8 8"><rect x=".5" y=".5" width="7" height="7" fill="none" stroke="#bbb"/><path d="M1.5 4l2 2 4-5" fill="none" stroke="#e8242a" stroke-width="1.3"/></svg>Pick Up the signs after the open house</li>
        <li><svg width="8" height="8" viewBox="0 0 8 8"><rect x=".5" y=".5" width="7" height="7" fill="none" stroke="#bbb"/><path d="M1.5 4l2 2 4-5" fill="none" stroke="#e8242a" stroke-width="1.3"/></svg>Store custom signs for you if needed</li>
      </ul>
      <span class="signup">SIGN UP</span>
      <p class="package-note">Sign Up For A Subscription And Get These Marketing Services For Free</p>
    </article>
    <article class="package">
      <div class="package-head"><svg width="110" height="54" viewBox="0 0 110 54"><path d="M0 0H110V50Q85 36 55 48T0 50Z" fill="#e8242a"/></svg><h3>20 SIGNS</h3></div>
      <ul class="features">
        <li><svg width="8" height="8" viewBox="0 0 8 8"><rect x=".5" y=".5" width="7" height="7" fill="none" stroke="#bbb"/><path d="M1.5 4l2 2 4-5" fill="none" stroke="#e8242a" stroke-width="1.3"/></svg>Place signs strategically in best areas according to where the open house is located</li>
        <li><svg width="8" height="8" viewBox="0 0 8 8"><rect x=".5" y=".5" width="7" height="7" fill="none" stroke="#bbb"/><path d="M1.5 4l2 2 4-5" fill="none" stroke="#e8242a" stroke-width="1.3"/></svg>Pick Up the signs after the open house</li>
        <li><svg width="8" height="8" viewBox="0 0 8 8"><rect x=".5" y=".5" width="7" height="7" fill="none" stroke="#bbb"/><path d="M1.5 4l2 2 4-5" fill="none" stroke="#e8242a" stroke-width="1.3"/></svg>Store custom signs for you if needed</li>
      </ul>
      <span class="signup">SIGN UP</span>
      <p class="package-note">Sign Up For A Subscription And Get These Marketing Services For Free</p>
    </article>
    <article class="package">
      <div class="package-head"><svg width="110" height="54" viewBox="0 0 110 54"><path d="M0 0H110V50Q85 36 55 48T0 50Z" fill="#e8242a"/></svg><h3>25 SIGNS</h3></div>
      <ul class="features">
        <li><svg width="8" height="8" viewBox="0 0 8 8"><rect x=".5" y=".5" width="7" height="7" fill="none" stroke="#bbb"/><path d="M1.5 4l2 2 4-5" fill="none" stroke="#e8242a" stroke-width="1.3"/></svg>Place signs strategically in best areas according to where the open house is located</li>
        <li><svg width="8" height="8" viewBox="0 0 8 8"><rect x=".5" y=".5" width="7" height="7" fill="none" stroke="#bbb"/><path d="M1.5 4l2 2 4-5" fill="none" stroke="#e8242a" stroke-width="1.3"/></svg>Pick Up the signs after the open house</li>
        <li><svg width="8" height="8" viewBox="0 0 8 8"><rect x=".5" y=".5" width="7" height="7" fill="none" stroke="#bbb"/><path d="M1.5 4l2 2 4-5" fill="none" stroke="#e8242a" stroke-width="1.3"/></svg>Store custom signs for you if needed</li>
      </ul>
      <span class="signup">SIGN UP</span>
      <p class="package-note">Sign Up For A Subscription And Get These Marketing Services For Free</p>
    </article>
  </div>
</section>

<footer class="site-footer">
  <div class="contact-row">
    <div class="contact address">
      <svg width="15" height="20" viewBox="0 0 15 20" fill="none" stroke="#e8242a" stroke-width="1.2"><path d="M7.5 19S1 11.5 1 7.5a6.5 6.5 0 0 1 13 0C14 11.5 7.5 19 7.5 19z"/><circle cx="7.5" cy="7.5" r="2.3"/></svg>
      <span>208, Lorem ipsum dolor<br>dosis suite - 48596</span>
    </div>
    <div class="contact phone">
      <svg width="20" height="20" viewBox="0 0 24 24" fill="none" stroke="#e8242a" stroke-width="1.3"><path d="M5 3h4l2 5-2.5 1.5a11 11 0 0 0 6 6L16 13l5 2v4a2 2 0 0 1-2 2A17 17 0 0 1 3 5a2 2 0 0 1 2-2z"/></svg>
      <span>Call Us<br>1800 555 0143 (toll-free)</span>
    </div>
    <div class="contact email">
      <svg width="21" height="20" viewBox="0 0 21 20" fill="none" stroke="#e8242a" stroke-width="1.2"><rect x="1" y="5" width="19" height="14"/><path d="M1 5l9.5 8L20 5"/><path d="M5 7V1h11v6"/></svg>
      <span>Email Us<br>info@tallyporchhelpers.net</span>
    </div>
  </div>
  <div class="social" aria-label="Social links"><span></span><span></span><span></span><span></span></div>
  <div class="footer-rule"></div>
  <div class="footer-brand"><i></i><b>Tally Porch</b></div>
  <div class="legal"><span>© 2018 TallyPorchHelpers</span><span>Privacy Policy &nbsp;Term of Service</span></div>
</footer>

</div>
</body>
</html>
```